Roofing Contractor business card redesign

I want to redesign my business card with a fresh, eye catching concept

Target Market(s)

Residential Roofing Clients, potential employees, and subcontractors.

Industry/Entity Type

Business

Colors

Designer to choose colors to be used in the design.

Requirements
Nice to have
• I just want something that's more pleasing to the eye. You can use a combination of either / or of my logos.

```html
<!DOCTYPE html>
<html lang="en">
<head>
<meta charset="utf-8">
<title>True Crew General Contractors – Business Card</title>
<link rel="stylesheet" href="https://fonts.googleapis.com/css2?family=Roboto+Condensed:wght@700&family=Roboto:wght@400;500;700&display=swap">
<style>
  :root {
    --backdrop: #e9e6e2;
    --orange: #e8711f;
    --yellow: #f5bf16;
    --brown: #4a1a12;
    --brown-soft: #6b4a3a;
    --card-white: #f5f5f4;
    --text-grey: #555555;
    --accent-orange: #e8742a;
  }
  * { box-sizing: border-box; margin: 0; padding: 0; }
  html, body { width: 1200px; height: 960px; overflow: hidden; }
  body {
    background: var(--backdrop);
    position: relative;
    font-family: "Roboto", Arial, sans-serif;
  }
  .card {
    position: absolute;
    left: 320px;
    width: 600px;
    height: 340px;
    border-radius: 18px;
    overflow: hidden;
  }
  .card-front {
    top: 106px;
    background: linear-gradient(100deg, var(--orange) 0 38%, var(--yellow) 38% 100%);
  }
  .front-emblem {
    position: absolute;
    left: 38px;
    top: 2px;
    width: 340px;
    height: 340px;
    border-radius: 50%;
    border: 7px solid #ffffff;
    box-shadow: 0 0 0 5px var(--brown);
    background: radial-gradient(circle at 50% 40%, #f7d77a 0%, #e89a3c 45%, #4a1a12 100%);
  }
  .front-brand {
    position: absolute;
    left: 382px;
    top: 230px;
    color: var(--brown);
  }
  .brand-name {
    font-family: "Roboto Condensed", "Arial Narrow", sans-serif;
    font-weight: 700;
    color: var(--brown);
    letter-spacing: -0.5px;
    line-height: 1;
  }
  .front-brand .brand-name { font-size: 48px; }
  .brand-sub {
    font-family: "Roboto", Arial, sans-serif;
    font-weight: 700;
    color: var(--brown);
    line-height: 1.1;
  }
  .front-brand .brand-sub { font-size: 15px; margin-top: 4px; }
  .front-web {
    font-size: 14px;
    letter-spacing: 2.4px;
    color: var(--brown-soft);
    margin-top: 6px;
  }

  .card-back {
    top: 493px;
    background: var(--card-white);
    box-shadow: 0 4px 8px rgba(0,0,0,0.25);
  }
  .back-brand {
    position: absolute;
    right: 36px;
    top: 44px;
    text-align: right;
  }
  .back-brand .brand-row {
    display: flex;
    align-items: center;
    justify-content: flex-end;
    gap: 6px;
  }
  .back-brand .brand-name { font-size: 44px; }
  .brand-dot {
    width: 40px; height: 40px;
    border-radius: 50%;
    background: var(--orange);
  }
  .back-brand .brand-sub { font-size: 17px; margin-top: 6px; }

  .contact {
    position: absolute;
    left: 35px;
    top: 122px;
  }
  .person-name {
    font-family: "Roboto Condensed", "Arial Narrow", sans-serif;
    font-weight: 700;
    font-size: 21px;
    color: var(--brown);
    letter-spacing: 0.2px;
  }
  .person-role {
    font-size: 15px;
    color: var(--accent-orange);
    line-height: 20px;
  }
  .address {
    font-size: 14px;
    color: var(--text-grey);
    line-height: 19px;
    margin-top: 6px;
  }
  .contact-list { list-style: none; margin-top: 9px; }
  .contact-list li {
    display: flex;
    align-items: center;
    gap: 8px;
    font-size: 14px;
    color: var(--text-grey);
    line-height: 19px;
  }
  .contact-list svg { width: 13px; height: 13px; fill: var(--brown); flex: none; }
</style>
</head>
<body>
  <section class="card card-front">
    <div class="front-emblem" role="img" aria-label="Illustration of three builders holding tools in front of a house roof"></div>
    <div class="front-brand">
      <div class="brand-name">True Crew</div>
      <div class="brand-sub">General Contractors, Inc.</div>
      <div class="front-web">www.truecrewtx.com</div>
    </div>
  </section>

  <section class="card card-back">
    <div class="back-brand">
      <div class="brand-row">
        <span class="brand-name">True</span>
        <span class="brand-dot"></span>
        <span class="brand-name">Crew</span>
      </div>
      <div class="brand-sub">General Contractors, Inc.</div>
    </div>

    <div class="contact">
      <div class="person-name">SAM HOLLIS</div>
      <div class="person-role">Board Certified Roof Inspector</div>
      <div class="person-role">Licensed Property Adjuster</div>
      <div class="address">4410 Maple Ridge Road Suite 118<br>Dallas, TX 75201</div>
      <ul class="contact-list">
        <li><svg viewBox="0 0 16 16"><path d="M3.5 1l3 3-1.7 2a9 9 0 0 0 5.2 5.2l2-1.7 3 3-2 2.5C6.5 15 1 9.5 1 3z"/></svg>(555) 014-2200</li>
        <li><svg viewBox="0 0 16 16"><path d="M4 0h8a1 1 0 0 1 1 1v14a1 1 0 0 1-1 1H4a1 1 0 0 1-1-1V1a1 1 0 0 1 1-1zm1 2v10h6V2zm3 11a1 1 0 1 0 0 2 1 1 0 0 0 0-2z"/></svg>(555) 017-3381</li>
        <li><svg viewBox="0 0 16 16"><path d="M1 3h14v10H1zm1.5 1.5v.3L8 9l5.5-4.2v-.3z"/></svg>sam@truecrewtx.com</li>
        <li><svg viewBox="0 0 16 16"><path d="M8 1a7 7 0 1 0 0 14A7 7 0 0 0 8 1zm0 2a5 5 0 0 1 4.6 3H10L8.5 4.5 6 5.5 7 8l-2 1 .5 3A5 5 0 0 1 8 3z"/></svg>www.truecrewtx.com</li>
      </ul>
    </div>
  </section>
</body>
</html>
```